Medical consulting firm needs polished website

I am a physician and working on setting up a smal consulting firm in New Hampshire, USA. It is called Bright Harbor Medical Services, LLC and the website will be BrightHarborMed.com. I was puttering around at making my own website, and it just didn't come together nicely so I've decided to leave it to the pros. The focus of the business is Advanced Care Planning, ie planning for your future medical needs. So it deals with some heavy stuff like planning for if you get sick, who should make decisions for you, end of life options etc. So it can't be too flippant or cutesy, but also can't be too dour and dark. I am hoping to convey that by thinking ahead and making some plans you can lift some of the worries off of yourself and your family - and that we can help make a scary sounding path more manageable. I want it to be made with wordpress and I have actually already bought a template ( Vitarun – A Modern Multidisciplinary Medical & Health Theme ). The website needs to have general information about our services, doc profile, appointment maker, blog/url link page, and ideally web commerce application ( the template has access to woocommerce). I've posted my business card and current brochure (still tweaking them, but you get the idea). I am also partnering with lumenfold.com and so have included their logo and would want connections/info about them. I have the logos etc in different formats as needed.

Target Market(s)

middle aged to older adults

Industry/Entity Type

Medical

Coding

Coded - Design and coding required

Font styles to use
Sans Serif

Requirements
Must have
• as above.
Nice to have
• Ease of reading/access for elderly viewers. woo commerce.

```html
<!DOCTYPE html>
<html lang="en">
<head>
<meta charset="utf-8">
<title>Bright Harbor Medical Services, LLC</title>
<link href="https://fonts.googleapis.com/css2?family=Montserrat:wght@400;600;700&family=Open+Sans:ital,wght@0,400;0,600;0,700;1,400&display=swap" rel="stylesheet">
<style>
:root{
  --blue:#1d5aa6;
  --blue-dark:#174a8a;
  --green:#3b9a33;
  --ink:#2b2b2b;
  --muted:#9a9a9a;
  --line:#e3e3e3;
  --soft:#f4f4f4;
  --white:#ffffff;
}
*{box-sizing:border-box;margin:0;padding:0}
html,body{width:1200px;height:4157px;overflow:hidden}
body{position:relative;background:var(--white);font-family:"Open Sans",Arial,sans-serif;color:var(--ink)}
.abs{position:absolute}
.head{font-family:"Montserrat",Arial,sans-serif}
.photo{position:absolute}

/* top bar */
.topbar{top:0;left:0;width:1200px;height:97px;border-bottom:1px solid var(--line)}
.brand{left:200px;top:24px;display:flex;align-items:center;gap:10px}
.brand-dot{width:44px;height:44px;border-radius:50%;background:var(--blue)}
.brand-name{font-family:"Montserrat",sans-serif;font-weight:700;font-size:15px;color:var(--blue);line-height:1.2;width:150px}
.info{top:32px;display:flex;gap:10px;font-size:10px;color:#666;line-height:1.45}
.info b{color:var(--ink);font-weight:600}
.info svg{flex:none}

/* nav */
.nav{top:97px;left:0;width:1200px;height:55px;border-bottom:1px solid var(--line)}
.menu{left:200px;top:0;height:55px;display:flex;align-items:center;gap:30px;font-family:"Montserrat",sans-serif;font-size:11px;font-weight:600;color:#444}
.menu .on{color:var(--blue)}
.nav-tool{top:0;height:55px;display:flex;align-items:center;justify-content:center;border-left:1px solid var(--line);font-size:11px;font-weight:600}
.book{left:798px;top:0;width:152px;height:55px;background:var(--blue);color:#fff;font-family:"Montserrat",sans-serif;font-size:10px;font-weight:700;display:flex;align-items:center;justify-content:center}

/* hero */
.hero{top:152px;left:0;width:1200px;height:516px;background:linear-gradient(90deg,#f2efea 0%,#ece6dd 35%,#d9c3a8 60%,#c9b6a2 80%,#e7e3df 100%)}
.hero h1{position:absolute;left:197px;top:195px;font-family:"Montserrat",sans-serif;font-weight:700;font-size:38px;line-height:42px;color:var(--blue)}
.hero p{position:absolute;left:197px;top:285px;font-size:17px;color:#555}
.btn-green{position:absolute;background:var(--green);color:#fff;font-family:"Montserrat",sans-serif;font-weight:700;font-size:11px;display:flex;align-items:center;justify-content:center}
.arrow{position:absolute;top:250px}

/* feature row */
.card-photo{height:175px;background:linear-gradient(135deg,#dfe7ee,#b8c9d8)}
.feature{position:absolute;top:743px;width:253px}
.feature h3{margin-top:14px;font-size:12px;font-weight:700;color:var(--blue);line-height:1.45}
.feature p{margin-top:10px;font-size:10px;color:var(--muted);line-height:1.6}
.hours{left:745px;top:743px;width:253px;height:318px;background:var(--blue);color:#fff;padding:28px 22px}
.hours h3{font-family:"Montserrat",sans-serif;font-size:18px;font-weight:700}
.hours p{margin-top:10px;font-size:10px;line-height:1.6;opacity:.9}
.hours-row{display:flex;justify-content:space-between;font-size:11px;font-weight:600;padding:14px 0;border-top:1px solid rgba(255,255,255,.25)}
.hours-row:first-of-type{margin-top:18px}

/* testimonial */
.quote-band{top:1117px;left:0;width:1200px;height:526px;background:linear-gradient(90deg,#3c3b39,#5a5753 45%,#4a4845 70%,#3a3937)}
.quote-band .veil{position:absolute;inset:0;background:rgba(30,30,30,.45)}
.quote-mark{left:0;width:1200px;top:135px;text-align:center;font-family:Georgia,serif;font-size:60px;font-weight:700;color:var(--green);line-height:1}
.quote-text{left:220px;width:760px;top:212px;text-align:center;font-style:italic;font-size:21px;line-height:1.55;color:#fff}
.quote-rule{left:370px;width:460px;top:355px;height:1px;background:rgba(255,255,255,.25)}
.quote-name{left:0;width:1200px;top:370px;text-align:center;color:#fff;font-family:"Montserrat",sans-serif;font-weight:700;font-size:24px}
.quote-role{left:0;width:1200px;top:405px;text-align:center;color:#ddd;font-size:14px}
.dots{left:585px;top:465px;display:flex;gap:6px}
.dots i{width:9px;height:9px;border-radius:50%;border:1px solid #bbb;display:block}
.dots i.on{background:#bbb}

/* services */
.svc-line{left:259px;top:1782px;width:1px;height:504px;background:var(--line)}
.svc-icon{position:absolute;left:204px;width:112px;height:112px;border-radius:50%;border:1px solid #ccc;background:#fff;display:flex;align-items:center;justify-content:center}
.svc-text{position:absolute;left:346px;width:260px}
.svc-text h3{font-family:"Montserrat",sans-serif;font-weight:700;font-size:15px;color:var(--blue)}
.svc-text p{margin-top:10px;font-size:12px;line-height:1.6;color:#aaa}
.nurse{left:665px;top:1676px;width:375px;height:734px;background:linear-gradient(180deg,#f7f5f3,#ece8e4 60%,#e3ded9)}

/* stories */
.stories{top:2410px;left:0;width:1200px;height:929px;background:var(--soft)}
.eyebrow{left:0;width:1200px;top:84px;text-align:center;font-size:12px;color:#777}
.stories h2{position:absolute;left:0;width:1200px;top:112px;text-align:center;font-family:"Montserrat",sans-serif;font-weight:700;font-size:20px;color:var(--blue)}
.tabs{left:0;width:1200px;top:162px;display:flex;justify-content:center;gap:30px;font-size:11px;color:#666}
.tabs .on{color:var(--blue);font-weight:700;border-bottom:2px solid var(--green);padding-bottom:6px}
.story{position:absolute;width:253px;height:300px;background:#fff}
.story .card-photo{height:178px}
.story h4{margin:20px 0 0 18px;font-family:"Montserrat",sans-serif;font-size:11px;font-weight:700;color:var(--blue)}
.story p{margin:8px 0 0 18px;font-size:10px;color:#aaa}
.btn-line{margin:18px 0 0 18px;width:82px;height:26px;border:1px solid var(--green);font-size:8px;font-weight:700;color:var(--green);display:flex;align-items:center;justify-content:center}
.play{position:absolute;left:106px;top:68px;width:42px;height:42px;border-radius:50%;border:2px solid #fff}
.play:after{content:"";position:absolute;left:15px;top:11px;border-left:13px solid #fff;border-top:8px solid transparent;border-bottom:8px solid transparent}

/* contact */
.contact h2{position:absolute;left:0;width:1200px;top:3412px;text-align:center;font-family:"Montserrat",sans-serif;font-weight:700;font-size:20px;color:var(--blue)}
.contact-sub{left:0;width:1200px;top:3450px;text-align:center;font-size:12px;color:#aaa}
.field{position:absolute;top:3505px;height:57px;border:1px solid var(--line);font-size:11px;color:#aaa;padding:0 18px;display:flex;align-items:center}
.partners{left:200px;width:798px;top:3622px;display:flex;justify-content:space-between;align-items:center}
.partner{width:120px;height:38px;background:#d3d3d3;border-radius:4px}

/* footer */
.footer{top:3741px;left:0;width:1200px;height:360px;background:var(--soft)}
.footer h5{font-family:"Montserrat",sans-serif;font-weight:700;font-size:12px;color:var(--blue)}
.f-about{left:200px;top:50px;width:190px;font-size:10px;color:#888;line-height:1.6}
.f-contact{display:flex;gap:10px;font-size:10px;color:#666;line-height:1.5;margin-top:14px}
.news-item{display:flex;gap:10px;margin-top:22px;font-size:10px;color:#777;line-height:1.45}
.news-item b{color:var(--blue);font-weight:600}
.post-item{display:flex;gap:10px;margin-top:18px;font-size:10px;color:#777;line-height:1.45}
.post-thumb{width:44px;height:44px;flex:none;background:linear-gradient(135deg,#c8b7a6,#8e7f73)}
.f-hours{left:812px;top:91px;width:186px;height:214px;background:var(--blue);color:#fff;padding:30px 16px 0}
.f-hours .badge{position:absolute;left:73px;top:-20px;width:40px;height:40px;border-radius:50%;background:var(--blue);border:2px solid #fff}
.f-row{display:flex;justify-content:space-between;font-size:9px;padding:4px 0;border-bottom:1px solid rgba(255,255,255,.2)}
.f-btn{margin:14px auto 0;width:140px;height:26px;background:#0e2f5c;font-size:8px;font-weight:700;display:flex;align-items:center;justify-content:center}
.bottom{top:4101px;left:0;width:1200px;height:56px;border-top:1px solid var(--line);display:flex;align-items:center;font-size:9px;color:#777}
</style>
</head>
<body>

<!-- top bar -->
<header class="abs topbar">
  <div class="abs brand"><span class="brand-dot"></span><span class="brand-name">Bright Harbor Medical Services, LLC</span></div>
  <div class="abs info" style="left:388px">
    <svg width="24" height="24" viewBox="0 0 24 24" fill="none" stroke="#3b9a33" stroke-width="1.5"><circle cx="12" cy="12" r="10"/><path d="M12 6v6l4 2"/></svg>
    <div><b>Monday - Friday 08:00 - 20:00</b><br>Saturday and Sunday - CLOSED</div>
  </div>
  <div class="abs info" style="left:604px">
    <svg width="24" height="24" viewBox="0 0 24 24" fill="none" stroke="#3b9a33" stroke-width="1.5"><path d="M5 3h4l2 5-3 2a11 11 0 0 0 6 6l2-3 5 2v4a2 2 0 0 1-2 2A18 18 0 0 1 3 5a2 2 0 0 1 2-2z"/></svg>
    <div><b>+1 603 - 555 - 0142</b><br>info@brightharbormed.com</div>
  </div>
  <div class="abs info" style="left:754px">
    <svg width="24" height="24" viewBox="0 0 24 24" fill="none" stroke="#3b9a33" stroke-width="1.5"><path d="M12 22s7-7 7-12a7 7 0 0 0-14 0c0 5 7 12 7 12z"/><circle cx="12" cy="10" r="2.5"/></svg>
    <div><b>12 Harbor Lane</b><br>Concord, NH 03301</div>
  </div>
  <div class="abs info" style="left:881px">
    <svg width="24" height="24" viewBox="0 0 24 24" fill="none" stroke="#3b9a33" stroke-width="1.5"><path d="M4 4h16v12H8l-4 4z"/></svg>
    <div><b>Connect With Us</b><br><span style="letter-spacing:3px;color:var(--blue)">●●●●●</span></div>
  </div>
</header>

<!-- navigation -->
<nav class="abs nav">
  <div class="abs menu"><span class="on">HOME</span><span>PAGES</span><span>PORTFOLIO</span><span>BLOG</span><span>ELEMENTS</span><span>SHOP</span></div>
  <div class="abs nav-tool" style="left:618px;width:56px">EN ▾</div>
  <div class="abs nav-tool" style="left:674px;width:62px"><svg width="16" height="16" viewBox="0 0 16 16" fill="none" stroke="#555" stroke-width="1.5"><circle cx="7" cy="7" r="5"/><path d="M11 11l4 4"/></svg></div>
  <div class="abs nav-tool" style="left:736px;width:62px"><svg width="14" height="16" viewBox="0 0 14 16" fill="none" stroke="#555" stroke-width="1.5"><path d="M2 5h10l-1 10H3z"/><path d="M4.5 5V3.5a2.5 2.5 0 0 1 5 0V5"/></svg></div>
  <div class="book">BOOK AN APPOINTMENT</div>
  <div class="abs nav-tool" style="left:950px;width:60px;border-right:1px solid var(--line)"><svg width="18" height="14" viewBox="0 0 18 14" stroke="#555" stroke-width="1.6"><path d="M0 1h18M0 7h18M0 13h18"/></svg></div>
</nav>

<!-- hero -->
<section class="abs hero" role="img" aria-label="Smiling carer embracing an elderly man">
  <svg class="arrow" style="left:92px" width="14" height="22" viewBox="0 0 14 22" fill="none" stroke="#fff" stroke-width="2"><path d="M12 2L3 11l9 9"/></svg>
  <svg class="arrow" style="left:1094px" width="14" height="22" viewBox="0 0 14 22" fill="none" stroke="#fff" stroke-width="2"><path d="M2 2l9 9-9 9"/></svg>
  <h1>ADVANCED<br>CARE PLANNING</h1>
  <p>Planning for your future medical needs</p>
  <div class="btn-green" style="left:197px;top:333px;width:150px;height:53px">LEARN MORE</div>
</section>

<!-- features -->
<article class="feature" style="left:200px">
  <div class="card-photo" role="img" aria-label="Doctor working at a laptop"></div>
  <h3>Neque porro quisquam est qui dolorem ipsum quia dolor sit amet</h3>
  <p>We guide families through each decision with care, so future wishes are clear, recorded and easy to share.</p>
</article>
<article class="feature" style="left:474px">
  <div class="card-photo" role="img" aria-label="Doctor reviewing notes on a tablet" style="background:linear-gradient(135deg,#eef1f3,#c7d1d9)"></div>
  <h3>Quisquam est qui dolorem ipsum quia dolor sit amet</h3>
  <p>Our physician meets with you to explain options, answer questions and prepare the documents you need.</p>
</article>
<aside class="abs hours">
  <h3>WORKING HOURS</h3>
  <p>Book a visit that suits your week. We keep time for calm, unhurried conversations about care.</p>
  <div class="hours-row"><span>Monday - Friday</span><span>9am-5pm</span></div>
  <div class="hours-row"><span>Saturday</span><span>9am-5pm</span></div>
  <div class="hours-row"><span>Sunday</span><span>Closed</span></div>
</aside>

<!-- testimonial -->
<section class="abs quote-band" role="img" aria-label="Older couple smiling together, darkened background">
  <div class="veil"></div>
  <div class="abs quote-mark">“</div>
  <p class="abs quote-text">Sed ut perspiciatis unde omnis iste natus error sit voluptatem accusantium doloremque laudantium, totam rem aperiam, eaque ipsa quae ab illo inventore veritatis et quasi architecto beatae...</p>
  <div class="abs quote-rule"></div>
  <div class="abs quote-name">Nora Whitfield,</div>
  <div class="abs quote-role">Mother Of Jackson, Newyork</div>
  <div class="abs dots"><i class="on"></i><i></i><i></i></div>
</section>

<!-- services -->
<div class="abs svc-line"></div>
<div class="svc-icon" style="top:1726px"><svg width="44" height="44" viewBox="0 0 44 44" fill="none" stroke="#3b9a33" stroke-width="2"><path d="M10 34C22 30 22 14 34 10M10 34c4-12 20-12 24-24"/><path d="M15 23l6 6M21 15l8 8M14 30l-3-3M30 14l3 3" stroke="#555" stroke-width="1.5"/></svg></div>
<div class="svc-text" style="top:1736px"><h3>MEDICAL TESTS</h3><p>Sed ut perspiciatis unde omnis iste natus error sit voluptatem accusantium</p></div>
<div class="svc-icon" style="top:1892px"><svg width="44" height="44" viewBox="0 0 44 44" fill="none" stroke="#555" stroke-width="1.6"><rect x="6" y="8" width="12" height="26" rx="6" transform="rotate(-35 12 21)"/><circle cx="30" cy="30" r="8"/><path d="M24 36l12-12"/></svg></div>
<div class="svc-text" style="top:1902px"><h3>MEDICINE CAN CURE YOUR</h3><p>Sed ut perspiciatis unde omnis iste natus error sit voluptatem accusantium</p></div>
<div class="svc-icon" style="top:2058px"><svg width="44" height="44" viewBox="0 0 44 44" fill="none" stroke="#555" stroke-width="1.6"><rect x="13" y="6" width="18" height="6"/><rect x="11" y="12" width="22" height="26" rx="2"/><path d="M22 20v10M17 25h10" stroke="#3b9a33"/></svg></div>
<div class="svc-text" style="top:2068px"><h3>BEST PRODUCT IN MEDICAL</h3><p>Sed ut perspiciatis unde omnis iste natus error sit voluptatem accusantium</p></div>
<div class="svc-icon" style="top:2230px"><svg width="44" height="44" viewBox="0 0 44 44" fill="none" stroke="#555" stroke-width="1.6"><path d="M12 6v10a8 8 0 0 0 16 0V6"/><path d="M20 24v6a8 8 0 0 0 16 0v-4"/><circle cx="36" cy="22" r="3" stroke="#3b9a33"/></svg></div>
<div class="svc-text" style="top:2240px"><h3>BEST DOCTORS TO CARE</h3><p>Sed ut perspiciatis unde omnis iste natus error sit voluptatem accusantium</p></div>
<div class="photo nurse" role="img" aria-label="Smiling nurse giving two thumbs up"></div>

<!-- stories -->
<section class="abs stories">
  <div class="abs eyebrow">Discover some amazing stories</div>
  <h2>WE ARE DIFFERENT AND PROUD TO BE. SEE WHY.</h2>
  <div class="abs tabs"><span class="on">All</span><span>Neurology</span><span>Orthopedics</span><span>Pediatrics</span><span>Surgery</span></div>

  <div class="story" style="left:200px;top:222px"><div class="card-photo" role="img" aria-label="Elderly couple at home" style="background:linear-gradient(135deg,#d9cbbd,#a99584)"></div><span class="play"></span><h4>TRUSTED ADVICE</h4><p>Sed ut perspiciatis unde omnis ...</p><div class="btn-line">LEARN MORE</div></div>
  <div class="story" style="left:474px;top:222px"><div class="card-photo" role="img" aria-label="Hands held in support" style="background:linear-gradient(135deg,#d8c2b2,#9d8070)"></div><h4>TRUSTED ADVICE</h4><p>Sed ut perspiciatis unde omnis ...</p><div class="btn-line">LEARN MORE</div></div>
  <div class="story" style="left:745px;top:222px"><div class="card-photo" role="img" aria-label="Senior woman smiling outdoors" style="background:linear-gradient(135deg,#c9cfae,#8b8f70)"></div><span class="play"></span><h4>TRUSTED ADVICE</h4><p>Sed ut perspiciatis unde omnis ...</p><div class="btn-line">LEARN MORE</div></div>

  <div class="story" style="left:200px;top:536px"><div class="card-photo" role="img" aria-label="Doctor consulting with a patient" style="background:linear-gradient(135deg,#e6e9ea,#b9c3c8)"></div><h4>TRUSTED ADVICE</h4><p>Sed ut perspiciatis unde omnis ...</p><div class="btn-line">LEARN MORE</div></div>
  <div class="story" style="left:474px;top:536px"><div class="card-photo" role="img" aria-label="Caring hands on an elderly hand" style="background:linear-gradient(135deg,#cdb5a3,#8a6e5e)"></div><span class="play"></span><h4>TRUSTED ADVICE</h4><p>Sed ut perspiciatis unde omnis ...</p><div class="btn-line">LEARN MORE</div></div>
  <div class="story" style="left:745px;top:536px"><div class="card-photo" role="img" aria-label="Carer helping an elderly woman" style="background:linear-gradient(135deg,#9fc4d6,#d6c2b3)"></div><h4>TRUSTED ADVICE</h4><p>Sed ut perspiciatis unde omnis ...</p><div class="btn-line">LEARN MORE</div></div>
</section>

<!-- contact -->
<section class="contact">
  <h2>NEED HELP FINDING THE RIGHT DOCTOR?</h2>
  <div class="abs contact-sub">Sed ut perspiciatis unde omnis iste natus error sit voluptatem</div>
  <div class="field" style="left:200px;width:320px">Name *</div>
  <div class="field" style="left:532px;width:315px">E-Mail *</div>
  <div class="btn-green" style="left:859px;top:3505px;width:139px;height:57px;font-size:14px">SEND</div>
  <div class="abs partners">
    <span class="partner"></span><span class="partner" style="width:90px"></span><span class="partner" style="width:160px"></span><span class="partner"></span><span class="partner" style="width:130px"></span>
  </div>
</section>

<!-- footer -->
<footer class="abs footer">
  <div class="abs f-about">
    <div class="brand" style="display:flex;align-items:center;gap:8px"><span class="brand-dot" style="width:36px;height:36px"></span><span class="brand-name" style="font-size:12px;width:140px">Bright Harbor Medical Services, LLC</span></div>
    <p style="margin-top:20px">Thoughtful advance care planning that lifts worry from you and your family, one clear step at a time.</p>
    <div class="f-contact"><svg width="18" height="18" viewBox="0 0 24 24" fill="none" stroke="#3b9a33" stroke-width="1.6"><path d="M5 3h4l2 5-3 2a11 11 0 0 0 6 6l2-3 5 2v4a2 2 0 0 1-2 2A18 18 0 0 1 3 5a2 2 0 0 1 2-2z"/></svg><div>+1 603 - 555 - 0142<br>info@brightharbormed.com</div></div>
    <div class="f-contact"><svg width="18" height="18" viewBox="0 0 24 24" fill="none" stroke="#3b9a33" stroke-width="1.6"><path d="M12 22s7-7 7-12a7 7 0 0 0-14 0c0 5 7 12 7 12z"/><circle cx="12" cy="10" r="2.5"/></svg><div>12 Harbor Lane<br>Concord, NH 03301</div></div>
  </div>
  <div class="abs" style="left:407px;top:90px;width:180px">
    <h5>LATEST NEWS</h5>
    <div class="news-item"><span style="color:#29a9e1">●</span><div>Vitarun - A Health &amp; Lifestyle<br><b>https://bhm.link/n1</b></div></div>
    <div class="news-item"><span style="color:#29a9e1">●</span><div>Vitarun - A Health &amp; Lifestyle<br><b>https://bhm.link/n2</b></div></div>
    <div class="news-item"><span style="color:#29a9e1">●</span><div>Vitarun - A Health &amp; Lifestyle<br><b>https://bhm.link/n3</b></div></div>
  </div>
  <div class="abs" style="left:610px;top:90px;width:180px">
    <h5>RECENT POSTS</h5>
    <div class="post-item"><span class="post-thumb" role="img" aria-label="Post thumbnail"></span><div><b style="color:#444">October 28th 2016</b><br>Planning ahead gives families peace.</div></div>
    <div class="post-item"><span class="post-thumb" role="img" aria-label="Post thumbnail"></span><div><b style="color:#444">October 28th 2016</b><br>Choosing who speaks for you.</div></div>
    <div class="post-item"><span class="post-thumb" role="img" aria-label="Post thumbnail"></span><div><b style="color:#444">October 28th 2016</b><br>Talking openly about care wishes.</div></div>
  </div>
  <div class="abs f-hours">
    <span class="badge"></span>
    <div class="f-row"><span>Monday</span><span>08am - 12pm</span></div>
    <div class="f-row"><span>Tuesday</span><span>08am - 12pm</span></div>
    <div class="f-row"><span>Wednesday</span><span>Free day</span></div>
    <div class="f-row"><span>Thursday</span><span>08am - 12pm</span></div>
    <div class="f-row"><span>Friday</span><span>08am - 12pm</span></div>
    <div class="f-row"><span>Saturday - Sunday</span><span>Closed</span></div>
    <div class="f-btn">MAKE AN APPOINTMENT</div>
  </div>
</footer>
<div class="abs bottom">
  <span style="position:absolute;left:200px;font-family:'Montserrat',sans-serif;font-weight:700;font-size:13px;color:var(--blue)">lumenfold.com</span>
  <span style="position:absolute;left:300px">© 2016 BRIGHT HARBOR | ALL RIGHTS RESERVED</span>
  <span style="position:absolute;left:632px;display:flex;gap:20px;font-weight:600"><span>HOME</span><span>PAGES</span><span>PORTFOLIO</span><span>BLOG</span><span>ELEMENTS</span><span>SHOP</span></span>
  <span style="position:absolute;left:955px;color:var(--green);letter-spacing:4px">●●●</span>
</div>

</body>
</html>
```